Personal training and nutrition business needs business card design

We need a business card that outlays our services and invites potential customers to join our team and take the first step to a healthier and more enjoyable life. We cater for any level of fitness and specialize in weight loss and conditioning, strength training, muscle gain and strength endurance. Whether you are just starting off or need some help getting to the next level of your journey we are here to get the job done.
We specialize in one on one or one on two personal training sessions and each program will be custom made to suit individual fitness goals of our clients

```html
<!DOCTYPE html>
<html lang="en">
<head>
<meta charset="utf-8">
<title>Stride &amp; Steady – Business Card</title>
<link rel="stylesheet" href="https://fonts.googleapis.com/css2?family=Lato:wght@400;700;900&family=Oswald:wght@400&display=swap">
<style>
  :root {
    --stage: #2a2a2c;
    --card-white: #ffffff;
    --card-black: #161617;
    --ink: #1a1a1a;
    --ink-soft: #3a3a3a;
    --purple: #8a4fb0;
    --purple-deep: #6b3fa0;
    --purple-light: #b45fb5;
    --rule: #9a9a9a;
  }
  * { box-sizing: border-box; margin: 0; padding: 0; }
  html, body { width: 1200px; height: 1108px; overflow: hidden; }
  body {
    background: var(--stage);
    font-family: "Lato", Arial, sans-serif;
    position: relative;
  }
  .card {
    position: absolute;
    top: 250px;
    width: 340px;
    height: 595px;
    border-radius: 18px;
    box-shadow: 0 18px 40px rgba(0,0,0,.45);
    overflow: hidden;
  }
  .card-front {
    left: 215px;
    background: var(--card-white);
    text-align: center;
    padding-top: 70px;
  }
  .card-back {
    left: 645px;
    background: var(--card-black);
  }

  /* brand */
  .brand-square {
    width: 44px; height: 44px;
    margin: 0 auto 22px;
    border-radius: 6px;
    background: linear-gradient(135deg, var(--purple-deep), var(--purple-light));
  }
  .brand-name {
    font-weight: 900;
    font-size: 44px;
    line-height: 0.98;
    color: var(--ink);
    letter-spacing: 1px;
    text-transform: uppercase;
  }
  .tagline {
    margin-top: 10px;
    font-family: "Oswald", "Arial Narrow", sans-serif;
    font-size: 12px;
    letter-spacing: 1.2px;
    color: var(--purple);
    text-transform: uppercase;
  }

  /* person */
  .person-name {
    margin-top: 34px;
    font-weight: 700;
    font-size: 26px;
    color: var(--purple);
    text-transform: uppercase;
    letter-spacing: .5px;
  }
  .person-role {
    font-size: 18px;
    color: var(--ink-soft);
    margin-top: 2px;
  }

  /* contact */
  .icon-row {
    display: flex;
    align-items: center;
    justify-content: center;
    gap: 6px;
    margin: 24px 28px 12px;
  }
  .icon-row .rule { flex: 1; height: 1px; background: var(--rule); }
  .icon-box {
    width: 26px; height: 26px;
    border-radius: 5px;
    background: var(--purple);
    display: flex; align-items: center; justify-content: center;
  }
  .icon-box svg { width: 16px; height: 16px; }
  .contact-line {
    font-size: 17px;
    color: var(--ink-soft);
    line-height: 1.45;
  }
  .divider {
    width: 230px; height: 1px;
    background: var(--rule);
    margin: 12px auto;
  }

  /* back */
  .back-pattern {
    position: absolute; inset: 0;
    background:
      radial-gradient(circle at 80% 10%, rgba(120,120,125,.35), transparent 55%),
      linear-gradient(160deg, #2b2b2e 0%, #1a1a1c 55%, #0f0f10 100%);
  }
  .back-brand {
    position: absolute;
    right: 36px;
    bottom: 150px;
    font-weight: 900;
    font-size: 14px;
    color: var(--purple);
    text-transform: uppercase;
    letter-spacing: .5px;
  }
</style>
</head>
<body>

<section class="card card-front" aria-label="Business card front">
  <div class="brand-square"></div>
  <h1 class="brand-name">Stride<br>&amp; Steady</h1>
  <p class="tagline">Personal training. &nbsp;Nutrition. Motivation</p>

  <h2 class="person-name">Marcus Hale</h2>
  <p class="person-role">Managing Director</p>

  <div class="icon-row">
    <span class="rule"></span>
    <span class="icon-box" aria-label="Phone">
      <svg viewBox="0 0 16 16"><path d="M4 2h2l1 3-1.5 1a8 8 0 0 0 4.5 4.5L11 9l3 1v2c0 1-1 2-2 2A10 10 0 0 1 2 4c0-1 1-2 2-2z" fill="#fff"/></svg>
    </span>
    <span class="icon-box" aria-label="Email">
      <svg viewBox="0 0 16 16"><rect x="2" y="4" width="12" height="8" fill="none" stroke="#fff" stroke-width="1.4"/><path d="M2 4l6 5 6-5" fill="none" stroke="#fff" stroke-width="1.4"/></svg>
    </span>
    <span class="icon-box" aria-label="Website">
      <svg viewBox="0 0 16 16"><circle cx="8" cy="8" r="5.5" fill="none" stroke="#fff" stroke-width="1.4"/><path d="M2.5 8h11M8 2.5c-2.5 3-2.5 8 0 11M8 2.5c2.5 3 2.5 8 0 11" fill="none" stroke="#fff" stroke-width="1.1"/></svg>
    </span>
    <span class="rule"></span>
  </div>

  <p class="contact-line">055-987 654 321</p>
  <p class="contact-line">hello@stridesteady.com</p>
  <p class="contact-line">www.stridesteady.com</p>
  <div class="divider"></div>
  <p class="contact-line">88 Harbour Lane</p>
  <p class="contact-line">10234, Northland</p>
</section>

<section class="card card-back" aria-label="Business card back">
  <div class="back-pattern" role="img" aria-label="Tonal gloss repeating brand monogram pattern on black"></div>
  <span class="back-brand">Stride &amp; Steady</span>
</section>

</body>
</html>
```